World travel poster - I want to remember where I've been!

I would like a poster for me to print and keep in my home as a record of my world travels. It must look like a mechanical sign in an airport (see picture for example) However I am flexible with exact layout, if you'd like to add images used to enhance poster etc. I have also uploaded some pictures from my travels if you would like to use some or all of them. They are named according to location.

Poster must include:
USA 2003
Malaysia 2006
Thailand 2007
Italy 2009
India, Vietnam, Hong Kong 2010
Bali 2011
Malaysia 2012
Singapore 2012
Vietnam, Cambodia, Laos 2013
Europe 2015

and the quote:

"The world is a book and those who do not travel read only one page."
― Severin of Caldra
Updates

Hi there. I have uploaded some photos of my travels to possibly use in my poster. They are named according to location. I haven't decided if I prefer the originial layout or with images, so please post both for me to consider. Thanks so much for your time to consider my project.

Target Market(s)

Something to catch the eye of visitors and remind me of my adventures.
A classic piece that is a conversation starter.

Industry/Entity Type

Airport

Font styles to use
Other font styles liked:
• Airport mechanical font

Requirements
Must have
• Some lettering like a mechanical airport board (see image attached for example).
Dimensions that are easy to print - either A3, or a long/narrow poster.
Nice to have
• A splash of colour or an image, maybe the words 'arrivals' or 'departures'

Use of some of my pictures if it doesn't look too busy.
Should not have
• Anything too over the top.

```html
<!DOCTYPE html>
<html lang="en">
<head>
<meta charset="utf-8">
<title>Travel Board Poster</title>
<link href="https://fonts.googleapis.com/css2?family=Bebas+Neue&family=Open+Sans:ital,wght@1,400&display=swap" rel="stylesheet">
<style>
  :root {
    --page: #f1f1f1;
    --board: #161616;
    --flap-top: #2c2c2c;
    --flap-mid: #151515;
    --flap-low: #1f1f1f;
    --flap-bottom: #0b0b0b;
    --flap-edge: #000;
    --flap-ink: #f4f4f4;
    --year-top: #ffffff;
    --year-mid: #e9e9e9;
    --year-low: #f6f6f6;
    --year-bottom: #d6d6d6;
    --year-ink: #1c1c1c;
    --quote-ink: #cfcfcf;
    --rule: #3a3a3a;
  }
  html, body {
    margin: 0;
    width: 1200px;
    height: 900px;
    overflow: hidden;
    background: var(--page);
  }
  .poster {
    position: absolute;
    left: 385px;
    top: 20px;
    width: 430px;
    height: 860px;
    background: var(--board);
    box-sizing: border-box;
    padding: 24px 18px 0;
  }
  .board {
    display: grid;
    row-gap: 7.4px;
  }
  .route {
    display: flex;
    gap: 1px;
    height: 44px;
  }
  .flap {
    position: relative;
    width: 27px;
    height: 44px;
    box-sizing: border-box;
    border: 1px solid var(--flap-edge);
    border-radius: 3px;
    background: linear-gradient(var(--flap-top), var(--flap-mid) 50%, var(--flap-low) 50%, var(--flap-bottom));
    color: var(--flap-ink);
    font-family: "Bebas Neue", sans-serif;
    font-size: 40px;
    line-height: 46px;
    text-align: center;
  }
  .flap::after {
    content: "";
    position: absolute;
    left: 0;
    right: 0;
    top: 50%;
    height: 1px;
    background: var(--flap-edge);
  }
  .flap--year {
    background: linear-gradient(var(--year-top), var(--year-mid) 50%, var(--year-low) 50%, var(--year-bottom));
    color: var(--year-ink);
  }
  .flap--year:first-of-type,
  .route .flap:nth-child(11) { margin-left: 2px; }
  .quote {
    position: absolute;
    left: 52px;
    right: 40px;
    top: 760px;
    padding: 12px 0 14px;
    border-top: 1px solid var(--rule);
    border-bottom: 1px solid var(--rule);
    font-family: "Open Sans", sans-serif;
    font-style: italic;
    color: var(--quote-ink);
    font-size: 13px;
    line-height: 17px;
    letter-spacing: 0.2px;
  }
  .quote__source {
    display: block;
    margin-top: 6px;
    font-style: normal;
    font-size: 8px;
    letter-spacing: 0.5px;
  }
</style>
</head>
<body>
<main class="poster">
  <section class="board" aria-label="Travel history">
    <div class="route"><span class="flap">U</span><span class="flap">S</span><span class="flap">A</span><span class="flap"></span><span class="flap"></span><span class="flap"></span><span class="flap"></span><span class="flap"></span><span class="flap"></span><span class="flap"></span><span class="flap flap--year">2</span><span class="flap flap--year">0</span><span class="flap flap--year">0</span><span class="flap flap--year">3</span></div>
    <div class="route"><span class="flap">M</span><span class="flap">A</span><span class="flap">L</span><span class="flap">A</span><span class="flap">Y</span><span class="flap">S</span><span class="flap">I</span><span class="flap">A</span><span class="flap"></span><span class="flap"></span><span class="flap flap--year">2</span><span class="flap flap--year">0</span><span class="flap flap--year">0</span><span class="flap flap--year">6</span></div>
    <div class="route"><span class="flap">T</span><span class="flap">H</span><span class="flap">A</span><span class="flap">I</span><span class="flap">L</span><span class="flap">A</span><span class="flap">N</span><span class="flap">D</span><span class="flap"></span><span class="flap"></span><span class="flap flap--year">2</span><span class="flap flap--year">0</span><span class="flap flap--year">0</span><span class="flap flap--year">7</span></div>
    <div class="route"><span class="flap">I</span><span class="flap">T</span><span class="flap">A</span><span class="flap">L</span><span class="flap">Y</span><span class="flap"></span><span class="flap"></span><span class="flap"></span><span class="flap"></span><span class="flap"></span><span class="flap flap--year">2</span><span class="flap flap--year">0</span><span class="flap flap--year">0</span><span class="flap flap--year">9</span></div>
    <div class="route"><span class="flap">I</span><span class="flap">N</span><span class="flap">D</span><span class="flap">I</span><span class="flap">A</span><span class="flap"></span><span class="flap"></span><span class="flap"></span><span class="flap"></span><span class="flap"></span><span class="flap flap--year">2</span><span class="flap flap--year">0</span><span class="flap flap--year">1</span><span class="flap flap--year">0</span></div>
    <div class="route"><span class="flap">V</span><span class="flap">I</span><span class="flap">E</span><span class="flap">T</span><span class="flap">N</span><span class="flap">A</span><span class="flap">M</span><span class="flap"></span><span class="flap"></span><span class="flap"></span><span class="flap flap--year">2</span><span class="flap flap--year">0</span><span class="flap flap--year">1</span><span class="flap flap--year">0</span></div>
    <div class="route"><span class="flap">H</span><span class="flap">O</span><span class="flap">N</span><span class="flap">G</span><span class="flap"></span><span class="flap">K</span><span class="flap">O</span><span class="flap">N</span><span class="flap">G</span><span class="flap"></span><span class="flap flap--year">2</span><span class="flap flap--year">0</span><span class="flap flap--year">1</span><span class="flap flap--year">0</span></div>
    <div class="route"><span class="flap">B</span><span class="flap">A</span><span class="flap">L</span><span class="flap">I</span><span class="flap"></span><span class="flap"></span><span class="flap"></span><span class="flap"></span><span class="flap"></span><span class="flap"></span><span class="flap flap--year">2</span><span class="flap flap--year">0</span><span class="flap flap--year">1</span><span class="flap flap--year">1</span></div>
    <div class="route"><span class="flap">M</span><span class="flap">A</span><span class="flap">L</span><span class="flap">A</span><span class="flap">Y</span><span class="flap">S</span><span class="flap">I</span><span class="flap">A</span><span class="flap"></span><span class="flap"></span><span class="flap flap--year">2</span><span class="flap flap--year">0</span><span class="flap flap--year">1</span><span class="flap flap--year">2</span></div>
    <div class="route"><span class="flap">S</span><span class="flap">I</span><span class="flap">N</span><span class="flap">G</span><span class="flap">A</span><span class="flap">P</span><span class="flap">O</span><span class="flap">R</span><span class="flap">E</span><span class="flap"></span><span class="flap flap--year">2</span><span class="flap flap--year">0</span><span class="flap flap--year">1</span><span class="flap flap--year">2</span></div>
    <div class="route"><span class="flap">V</span><span class="flap">I</span><span class="flap">E</span><span class="flap">T</span><span class="flap">N</span><span class="flap">A</span><span class="flap">M</span><span class="flap"></span><span class="flap"></span><span class="flap"></span><span class="flap flap--year">2</span><span class="flap flap--year">0</span><span class="flap flap--year">1</span><span class="flap flap--year">3</span></div>
    <div class="route"><span class="flap">C</span><span class="flap">A</span><span class="flap">M</span><span class="flap">B</span><span class="flap">O</span><span class="flap">D</span><span class="flap">I</span><span class="flap">A</span><span class="flap"></span><span class="flap"></span><span class="flap flap--year">2</span><span class="flap flap--year">0</span><span class="flap flap--year">1</span><span class="flap flap--year">3</span></div>
    <div class="route"><span class="flap">L</span><span class="flap">A</span><span class="flap">O</span><span class="flap">S</span><span class="flap"></span><span class="flap"></span><span class="flap"></span><span class="flap"></span><span class="flap"></span><span class="flap"></span><span class="flap flap--year">2</span><span class="flap flap--year">0</span><span class="flap flap--year">1</span><span class="flap flap--year">3</span></div>
    <div class="route"><span class="flap">E</span><span class="flap">U</span><span class="flap">R</span><span class="flap">O</span><span class="flap">P</span><span class="flap">E</span><span class="flap"></span><span class="flap"></span><span class="flap"></span><span class="flap"></span><span class="flap flap--year">2</span><span class="flap flap--year">0</span><span class="flap flap--year">1</span><span class="flap flap--year">5</span></div>
  </section>
  <blockquote class="quote">
    "THE WORLD IS A BOOK AND THOSE WHO DO NOT TRAVEL READ ONLY ONE PAGE."
    <span class="quote__source">— SEVERIN OF CALDRA</span>
  </blockquote>
</main>
</body>
</html>
```